Need a design for coffee shop/bar

We need a simple site designed for a local coffee shop and bar. Small, locally owned place. Has live entertainment on occasion. Serves the business lunch and happy hour crowd as well and the baseball and basketball games fans. Located in downtown Cleveland. Looking for a simple site design with logo at top, horizontal main nav and slideshow and will need an interior page design as well (which will be used for general content like about, contact, menu, events, etc.) Would like it to be responsive. Current site is bvmelkins.com. Owner likes the color scheme, but open to changes.

*note - the owner roasts his own coffee and has a sister company for this called Harrow Bean Works (harrowbeanworks.com). We plan to use the exact same design for the coffee company's website, expect we'll swap out the logo at the top and use different photos. As part of the project we'd like a page designed that displays the various coffee products, but do not require this specific site be designed.

So, that makes three pages total. Home page (bvmelkins.com), interior and product page.

Target Market(s)

Young professionals, hipsters, sports fans, coffee and beer enthusiasts. Owner is into reggae and often has reggae bands.

Industry/Entity Type

Entertainment

Number of Pages Required

3 page

Requirements
Must have
• Slideshow, lot of images (some examples are on the current site, bvmelkins.com - client will be providing us with higher resolution images when we start development, so place holders are fine for the design). Responsive.

```html
<!DOCTYPE html>
<html lang="en">
<head>
<meta charset="utf-8">
<title>B.V. Melkin's — Coffee &amp; Bar</title>
<link rel="stylesheet" href="https://fonts.googleapis.com/css2?family=Questrial&family=Open+Sans:wght@400;600&family=Oswald:wght@300;400&family=Noto+Serif&display=swap">
<style>
:root{
  --black:#000;
  --dark:#232323;
  --dark-2:#2c2c2c;
  --orange:#e9a131;
  --orange-deep:#d48f22;
  --accent:#f2a634;
  --ink:#1c1c1c;
  --muted:#8d8d8d;
  --light:#f2f2f2;
  --white:#fff;
  --green:#8ccf8c;
}
*{box-sizing:border-box;margin:0;padding:0}
html,body{width:710px;height:1200px;overflow:hidden}
body{position:relative;font-family:"Open Sans",sans-serif;background:var(--dark);color:var(--white)}
h1,h2,h3{font-weight:400}
.abs{position:absolute}

/* header */
.site-header{left:0;top:0;width:710px;height:57px;background:var(--black)}
.brand{left:58px;top:16px;font-family:"Questrial",sans-serif;font-size:21px;color:var(--accent);letter-spacing:.5px}
.main-nav{right:58px;top:0;height:57px;display:flex;align-items:center;font-family:"Questrial",sans-serif;font-size:9.5px}
.main-nav a{color:var(--white);text-decoration:none;padding:0 13px;border-left:1px solid #3a2a10;line-height:30px}
.main-nav a:first-child{border-left:none}

/* hero */
.hero{left:0;top:57px;width:710px;height:346px;background:linear-gradient(180deg,#7a4a22 0%,#a8703c 35%,#6b4a2c 70%,#4d3a2a 100%)}
.hero-caption{left:58px;top:214px;width:236px;height:84px;background:rgba(40,30,20,.55);padding:8px 14px}
.hero-caption h1{font-family:"Questrial",sans-serif;font-size:25px;color:var(--accent);letter-spacing:.5px}
.hero-caption p{font-size:8px;line-height:13px;color:var(--white);margin-top:3px}
.hero-arrow{top:228px;width:24px;height:24px;border-radius:50%;background:rgba(40,40,40,.7)}

/* reservation bar */
.reserve{left:58px;top:371px;width:594px;height:59px;background:var(--orange);display:flex;align-items:center;gap:9px;padding:0 10px;box-shadow:0 2px 4px rgba(0,0,0,.3)}
.field{width:108px;height:25px;border:1px solid #c98a25;background:var(--orange);font-size:7.5px;color:#3a2a10;display:flex;align-items:center;justify-content:space-between;padding:0 7px}
.reserve-btn{margin-left:auto;width:108px;height:26px;background:var(--dark);color:var(--white);font-family:"Questrial",sans-serif;font-size:11px;display:flex;align-items:center;justify-content:center;border-radius:2px}

/* lunch picks */
.dish{top:462px;width:185px}
.dish h2{font-family:"Questrial",sans-serif;font-size:13px;color:var(--accent)}
.dish-photo{position:relative;margin-top:13px;height:124px;border:3px solid #111}
.serve-tag{position:absolute;right:2px;top:2px;background:rgba(40,40,40,.85);padding:3px 6px;text-align:center;font-family:"Noto Serif",serif}
.serve-tag small{display:block;font-size:5.5px;color:#bbb}
.serve-tag b{font-size:8px;color:var(--accent);font-weight:400}
.dish p{margin-top:10px;font-size:6.3px;line-height:12px;color:var(--muted)}

/* info band */
.info-band{left:0;top:712px;width:710px;height:266px;background:var(--orange);color:var(--ink)}
.band-title{top:28px;font-family:"Questrial",sans-serif;font-size:12.5px;letter-spacing:.3px}
.about-photo{left:58px;top:56px;width:185px;height:124px;border:3px solid #ddd;background:linear-gradient(180deg,#3d2a1a,#1f4a2a 55%,#2b2b20)}
.about-text{left:58px;top:188px;width:190px;font-size:6.3px;line-height:12px}
.specials{left:261px;top:54px;width:186px;height:176px;background:var(--orange-deep);padding:8px 9px}
.specials h3{font-family:"Questrial",sans-serif;font-size:12px;margin-bottom:5px}
.specials ul{list-style:none;font-family:"Oswald",sans-serif;font-weight:300;font-size:7.6px;color:var(--white)}
.specials li{display:flex;align-items:center;gap:8px;height:20.4px;white-space:nowrap}
.specials li::before{content:"";flex:none;width:6px;height:6px;border:1px solid var(--white);border-radius:50%}
.specials p{font-family:"Oswald",sans-serif;font-weight:300;font-size:7.3px;line-height:15px;color:var(--white);margin-top:5px}
.testimonial-title{left:467px;top:27px;font-family:"Noto Serif",serif;font-size:12px}
.quote{left:467px;top:55px;width:185px;height:110px;background:var(--light);padding:13px 12px;font-size:6.3px;line-height:14px;color:#555}
.quote span{font-family:"Noto Serif",serif;font-size:20px;color:#bbb;line-height:6px;vertical-align:-6px;margin-right:6px}
.avatar{left:467px;top:181px;width:46px;height:46px;border-radius:50%;background:linear-gradient(180deg,#e8e8e8,#9a9a9a)}
.author{left:524px;top:185px;width:128px;font-size:7px;font-style:italic;border-bottom:1px solid #cf8f2a;padding-bottom:6px}
.author em{color:#7a5a1a}
.pager{top:211px;width:12px;height:11px;background:var(--white)}

/* newsletter */
.newsletter{left:0;top:978px;width:710px;height:54px;background:var(--dark-2)}
.social{left:58px;top:0;width:150px;height:54px;background:#333;display:flex;align-items:center;justify-content:center;gap:15px}
.social i{width:8px;height:8px;border-radius:50%;background:var(--white);display:block}
.mail-icon{left:220px;top:13px;width:28px;height:28px}
.news-head{left:264px;top:12px;font-family:"Noto Serif",serif;font-size:13px}
.news-sub{left:264px;top:32px;font-size:8.5px}
.name-input{left:439px;top:15px;width:137px;height:26px;background:var(--white);color:#777;font-size:7.5px;padding:9px 7px}
.subscribe{left:576px;top:15px;width:76px;height:26px;background:var(--green);font-family:"Questrial",sans-serif;font-size:9px;display:flex;align-items:center;justify-content:center}

/* footer */
.site-footer{left:0;top:1032px;width:710px;height:134px;background:var(--light);color:#333}
.footer-brand{left:58px;top:52px;font-family:"Questrial",sans-serif;font-size:17px;color:var(--ink)}
.divider{top:16px;width:1px;height:108px;background:#ddd}
.footer-title{top:14px;font-family:"Questrial",sans-serif;font-size:12.5px}
.hours{top:45px;font-size:7px;line-height:14.5px}
.contact-line{left:504px;font-size:7.5px;line-height:12px}
.contact-line svg{vertical-align:middle;margin-right:8px}

.copyright{left:0;top:1166px;width:710px;height:34px;background:var(--dark);font-size:8px;display:flex;align-items:center;justify-content:center}
</style>
</head>
<body>

<header class="site-header abs">
  <div class="brand abs">B.V. MELKIN'S</div>
  <nav class="main-nav abs">
    <a href="#">Home</a><a href="#">About Us</a><a href="#">Packages</a><a href="#">Events</a><a href="#">Reservations</a><a href="#">Contact</a>
  </nav>
</header>

<section class="hero abs" role="img" aria-label="Slideshow photo of the wood-panelled bar and dining room with tables and upholstered chairs"></section>
<div class="hero-caption abs">
  <h1>B.V. MELKIN'S</h1>
  <p>Duis aute irure dolor in reprehenderit in voluptate velit esse cillum dolore eu fugiat nulla pariatur. Excepteur sint occaecat cupidatat</p>
</div>
<div class="hero-arrow abs" style="left:22px"><svg width="24" height="24"><path d="M14 7l-5 5 5 5" stroke="#fff" stroke-width="2" fill="none"/></svg></div>
<div class="hero-arrow abs" style="left:662px"><svg width="24" height="24"><path d="M10 7l5 5-5 5" stroke="#fff" stroke-width="2" fill="none"/></svg></div>

<form class="reserve abs">
  <div class="field">Visit Date <svg width="7" height="7"><rect x="0.5" y="1.5" width="6" height="5" fill="none" stroke="#3a2a10"/></svg></div>
  <div class="field">Time <svg width="7" height="7"><circle cx="3.5" cy="3.5" r="3" fill="none" stroke="#3a2a10"/><path d="M3.5 1.8v1.9h1.4" stroke="#3a2a10" fill="none"/></svg></div>
  <div class="field">Guests <svg width="6" height="4"><path d="M0 0h6L3 4z" fill="#3a2a10"/></svg></div>
  <div class="field">Occasion <svg width="6" height="4"><path d="M0 0h6L3 4z" fill="#3a2a10"/></svg></div>
  <div class="reserve-btn">Reserve a Table</div>
</form>

<article class="dish abs" style="left:58px">
  <h2>Hometeamer - $8</h2>
  <div class="dish-photo" role="img" aria-label="Photo of the café storefront with a crowd outside" style="background:linear-gradient(180deg,#5a4a3a,#7a6a5a 50%,#4a5a6a)">
    <div class="serve-tag"><small>LUNCH</small><b>11A - 3P</b></div>
  </div>
  <p>Lorem ipsum dolor sit amet, consectetur adipisicing elit, sed do eiusmod tempor incididunt ut labore et dolore magna aliqua. Ut enim ad minim veniam, Lorem ipsum dolor sit amet, consectetur adipisicing</p>
</article>
<article class="dish abs" style="left:264px">
  <h2>The Jake - $7.50</h2>
  <div class="dish-photo" role="img" aria-label="Photo of a pizza beside a dark beer" style="background:linear-gradient(180deg,#1a1a1a 40%,#a0401e 75%,#7a2a14)">
    <div class="serve-tag"><small>LUNCH</small><b>11A - 3P</b></div>
  </div>
  <p>Lorem ipsum dolor sit amet, consectetur adipisicing elit, sed do eiusmod tempor incididunt ut labore et dolore magna aliqua. Ut enim ad minim veniam, Lorem ipsum dolor sit amet, consectetur adipisicing</p>
</article>
<article class="dish abs" style="left:466px">
  <h2>Baked Artichoke - $7.25</h2>
  <div class="dish-photo" role="img" aria-label="Photo of a platter of cheese, olives, cured meat and crackers" style="background:linear-gradient(180deg,#c89a5a,#efe2c0 45%,#d89080 80%,#c8a070)">
    <div class="serve-tag"><small>HAPPY HOUR</small><b>4P - 7P</b></div>
  </div>
  <p>Lorem ipsum dolor sit amet, consectetur adipisicing elit, sed do eiusmod tempor incididunt ut labore et dolore magna aliqua. Ut enim ad minim veniam, Lorem ipsum dolor sit amet, consectetur adipisicing</p>
</article>

<section class="info-band abs">
  <h2 class="band-title abs" style="left:58px">ABOUT THE B.V. MELKIN'S</h2>
  <div class="about-photo abs" role="img" aria-label="Photo of the front entrance with a green striped awning"></div>
  <p class="about-text abs">Lorem ipsum dolor sit amet, consectetur adipisicing elit, sed do eiusmod tempor incididunt ut labore et dolore magna aliqua. Ut enim ad minim veniam, Lorem ipsum dolor sit amet, consectetur adipisicing</p>

  <h2 class="band-title abs" style="left:261px">OUR MENU</h2>
  <div class="specials abs">
    <h3>DAILY SPECIALS</h3>
    <ul>
      <li>Monday - Turkey Club w side $6.75</li>
      <li>Tuesday - Tuna Melt w side $6.50</li>
      <li>Wednesday - The Jake w side $6.50</li>
      <li>Thursday - Corned Beef or Turkey Reubens w side $7</li>
      <li>Friday - Grilled Cheese and Tomato Soup $6</li>
    </ul>
    <p>Daily soup with the option of a half traditional sandwich.<br>We feature premium Hartfield Deli.</p>
  </div>

  <h2 class="testimonial-title abs">Customers Testimonials</h2>
  <blockquote class="quote abs"><span>&ldquo;</span>Lorem ipsum dolor sit amet, consectetur adipiscing elit, sed do eiusmod tempor incididunt ut labore et dolore magna aliqua. Ut enim ad minim veniam, quis nostrud exercitation Lorem ipsum dolor sit amet,</blockquote>
  <div class="avatar abs" role="img" aria-label="Customer portrait"></div>
  <div class="author abs">John Doe <em>- B.V. Melkin's</em></div>
  <div class="pager abs" style="left:524px"><svg width="12" height="11"><path d="M7 3L4 5.5 7 8" stroke="#222" fill="none"/></svg></div>
  <div class="pager abs" style="left:540px"><svg width="12" height="11"><path d="M5 3l3 2.5L5 8" stroke="#222" fill="none"/></svg></div>
</section>

<section class="newsletter abs">
  <div class="social abs" aria-label="Social links"><i></i><i></i><i></i><i></i><i></i></div>
  <svg class="mail-icon abs" viewBox="0 0 28 28"><circle cx="14" cy="14" r="13" fill="none" stroke="#fff" stroke-width="1.2"/><rect x="8" y="10" width="12" height="9" fill="none" stroke="#fff" stroke-width="1.2"/><path d="M8 10l6 5 6-5" stroke="#fff" stroke-width="1.2" fill="none"/></svg>
  <div class="news-head abs">Join our Newsletter.</div>
  <div class="news-sub abs">Stay up to date with the latest news.</div>
  <div class="name-input abs">Name</div>
  <div class="subscribe abs">SUBSCRIBE</div>
</section>

<footer class="site-footer abs">
  <div class="footer-brand abs">Harrow Bean Works</div>
  <div class="divider abs" style="left:217px"></div>
  <h3 class="footer-title abs" style="left:261px">Open Hour</h3>
  <div class="hours abs" style="left:261px">Monday 7a - 9p<br>T - F 7a - midnight ...<br>Sat - 8a - midnight ...<br>Sun - 8a - 2p</div>
  <div class="hours abs" style="left:358px">HAPPY HOUR:<br>Monday - Happy Hour all night!<br>Tu - Fri - 4p to 7p</div>
  <div class="divider abs" style="left:476px"></div>
  <h3 class="footer-title abs" style="left:504px">Contact Information</h3>
  <div class="contact-line abs" style="top:43px">18 Lantern Row, Suite 4,<br>Eastbrook, OH 44190-0000</div>
  <div class="contact-line abs" style="top:73px;font-size:8.5px"><svg width="11" height="11" viewBox="0 0 11 11"><path d="M2 1l2 0 1 2.5-1.3 1a6 6 0 0 0 2.8 2.8l1-1.3 2.5 1v2a1 1 0 0 1-1 1A8.5 8.5 0 0 1 1 2a1 1 0 0 1 1-1z" fill="none" stroke="#8ccf8c"/></svg>555-210-4418 or 555-210-4419</div>
  <div class="contact-line abs" style="top:89px;font-size:8px"><svg width="11" height="9" viewBox="0 0 11 9"><rect x=".5" y=".5" width="10" height="8" fill="none" stroke="#8ccf8c"/><path d="M.5 .5l5 4 5-4" fill="none" stroke="#8ccf8c"/></svg>info@bvmelkins.com</div>
</footer>

<div class="copyright abs">Copyright©2015 B.V. Melkin's</div>

</body>
</html>
```